Aerial Imaging and photgraphy business card

Design a business card with eye catching aerial photo of country side / landscape with a drone in the foreground.
Also contact details.

Target Market(s)

Aerial Imaging photography

Industry/Entity Type

Advertising

Contact Information for Business Card

Rowland
0412965203
Website http://www.skywardvistaphoto.com.au/
email address : skywardvistaphoto.com.au

Colors
e8f1ca
cadf82
9bcb3c
33a6d7
85cae6
cee9f5

Requirements
Must have
• High res photo
• Korvane drone in the foreground Either T4200 and korvane Glidewing or both
Nice to have
• high resolution landscape country photo on the front of the card with a Korvane T4200 drone in the foreground.

```html
<!DOCTYPE html>
<html lang="en">
<head>
<meta charset="utf-8">
<title>Skyward Vista Photo – Business Card</title>
<link href="https://fonts.googleapis.com/css2?family=Roboto:wght@400;500;700&display=swap" rel="stylesheet">
<style>
  :root {
    --page: #dcdcdc;
    --card: #ffffff;
    --ink: #2f2f2f;
    --ink-soft: #4a4a4a;
    --icon-blue: #2f80c4;
    --web-green: #2e9b3c;
    --brand-red: #b3232a;
    --accent-teal: #2f93b0;
    --accent-dark: #173c4c;
    --sky-top: #a9cbe6;
    --sky-haze: #dfe8ee;
    --field-green: #6f9a4a;
    --forest: #3c5a2e;
  }
  * { box-sizing: border-box; margin: 0; padding: 0; }
  html, body {
    width: 1200px; height: 1200px; overflow: hidden;
    background: var(--page);
    font-family: "Roboto", Arial, sans-serif;
  }
  .stage {
    position: relative; width: 1200px; height: 1200px;
    display: flex; flex-direction: column; align-items: center; justify-content: center;
    gap: 48px;
  }
  .card {
    position: relative; width: 760px; height: 422px;
    border-radius: 14px; overflow: hidden;
    background: var(--card);
    box-shadow: 0 4px 14px rgba(0,0,0,0.18);
  }
  .card-front__photo {
    width: 100%; height: 100%;
    background:
      linear-gradient(180deg, var(--sky-top) 0%, var(--sky-haze) 38%, var(--sky-haze) 46%, var(--field-green) 62%, var(--forest) 100%);
  }
  .accent-bar {
    position: absolute; left: 0; top: 84px; width: 18px; height: 62px;
    background: linear-gradient(180deg, var(--accent-teal), var(--accent-dark));
  }
  .person { position: absolute; left: 64px; top: 84px; }
  .person__name { font-size: 30px; font-weight: 700; color: var(--ink); line-height: 1.1; }
  .person__title { font-size: 16px; font-weight: 400; color: var(--ink-soft); margin-top: 4px; }
  .brand {
    position: absolute; right: 44px; top: 46px;
    display: flex; align-items: center; gap: 12px;
  }
  .brand__dot { width: 26px; height: 26px; border-radius: 50%; background: var(--brand-red); }
  .brand__name { font-size: 22px; font-weight: 700; color: var(--brand-red); letter-spacing: 0.5px; }
  .contacts {
    position: absolute; left: 64px; bottom: 40px;
    list-style: none; font-size: 17px; color: var(--ink);
  }
  .contacts li { display: flex; align-items: center; gap: 12px; height: 27px; }
  .contacts svg { width: 16px; height: 16px; fill: var(--icon-blue); flex: none; }
  .contacts .web-mid { color: var(--web-green); }
</style>
</head>
<body>
<main class="stage">
  <section class="card card-front">
    <div class="card-front__photo" role="img" aria-label="Aerial photograph of green countryside and a hazy lake with a camera drone flying in the foreground"></div>
  </section>

  <section class="card card-back">
    <div class="brand">
      <span class="brand__dot"></span>
      <span class="brand__name">Skyward Vista Photo</span>
    </div>

    <div class="accent-bar"></div>
    <div class="person">
      <h1 class="person__name">Callum Hartley</h1>
      <p class="person__title">Managing Director</p>
    </div>

    <ul class="contacts">
      <li>
        <svg viewBox="0 0 24 24" aria-hidden="true"><path d="M6.6 10.8a15.1 15.1 0 0 0 6.6 6.6l2.2-2.2a1 1 0 0 1 1-.25 11.4 11.4 0 0 0 3.6.57 1 1 0 0 1 1 1V20a1 1 0 0 1-1 1A17 17 0 0 1 3 4a1 1 0 0 1 1-1h3.5a1 1 0 0 1 1 1c0 1.25.2 2.45.57 3.57a1 1 0 0 1-.25 1z"/></svg>
        <span>0412965203</span>
      </li>
      <li>
        <svg viewBox="0 0 24 24" aria-hidden="true"><path d="M2 5h20v14H2z M3.5 6.5 12 13l8.5-6.5" /><path d="M2 5h20v2l-10 7L2 7z" fill="#fff" opacity=".0"/></svg>
        <span>hello@skywardvistaphoto.com.au</span>
      </li>
      <li>
        <svg viewBox="0 0 24 24" aria-hidden="true"><path d="M12 2a10 10 0 1 0 0 20 10 10 0 0 0 0-20zm6.9 6h-3a15 15 0 0 0-1.3-3.9A8 8 0 0 1 18.9 8zM12 4a13 13 0 0 1 1.9 4h-3.8A13 13 0 0 1 12 4zM4.3 14a8 8 0 0 1 0-4h3.4a16 16 0 0 0 0 4zm.8 2h3a15 15 0 0 0 1.3 3.9A8 8 0 0 1 5.1 16zm3-8h-3a8 8 0 0 1 4.3-3.9A15 15 0 0 0 8.1 8zM12 20a13 13 0 0 1-1.9-4h3.8A13 13 0 0 1 12 20zm2.3-6H9.7a14 14 0 0 1 0-4h4.6a14 14 0 0 1 0 4zm.3 5.9a15 15 0 0 0 1.3-3.9h3a8 8 0 0 1-4.3 3.9zm1.7-5.9a16 16 0 0 0 0-4h3.4a8 8 0 0 1 0 4z"/></svg>
        <span>www.<span class="web-mid">skywardvistaphoto</span>.com.au</span>
      </li>
      <li>
        <svg viewBox="0 0 24 24" aria-hidden="true"><path d="M12 2a7 7 0 0 0-7 7c0 5.25 7 13 7 13s7-7.75 7-13a7 7 0 0 0-7-7zm0 9.5A2.5 2.5 0 1 1 12 6.5a2.5 2.5 0 0 1 0 5z"/></svg>
        <span>Marrindale NSW 2594, Australia</span>
      </li>
    </ul>
  </section>
</main>
</body>
</html>
```